Geschäftspapiere für Termin Startup
Zielgruppe
Wir sind ein Startup, das über die Seite Buchlotte.de (derzeit noch in der Beta-Phase)zukünftig folgenden Service anbietet: Unternehmer können sehr flexibel (selbst) gestaltete Terminformulare erstellen und auf Ihrer Website einbinden. Kunden können dann diese Termine buchen und bekommen dann Erinnerungs-Mails und SMS.
Zielgruppe: Dienstleister wie Fotografen, Friseure, Versicherungsvertreter, Masseure, Restaurants, Arztpraxen. Also alle, die darauf angewiesen sind, dass vereinbarte Termine eingehalten werden und die die Terminvereinbarung vereinfachen wollen. Also weniger per Telefon, mehr über die eigene Website.
Dateien bitte beachten für die Ansicht des Look & Feels:
https://ablage.wolkenfach.de/open?id=7QwerT2zuIopAs9dFgHjKl4YxCvbNm3Pk
Bonus-Aktion: Wir zahlen pauschal jeweils 30,00 Euro an die Designer auf den Plätzen 2 bis 4 für die geleistete Arbeit. Nur einer kann gewinnen und den Zuschlag bekommen. Aber so möchten wir gerne die Arbeit dennoch honorieren.
Aufgabenstellung
Wir benötigen ein modernes Briefpapier-Layout passend zu unserem CD.
Gerne darf/soll der BOMMEL (siehe Maskottchen in https://ablage.wolkenfach.de/open?id=5RtzUi8oPasDfGhJkL2yXcVbNmQwE4rTz )darauf erscheinen.
Maskottchen BOMMEL gibt es in mehreren Varianten. Siehe https://ablage.wolkenfach.de/ordner/folders/6PlmOknIjbUhYgTfRdEsWaQz2Xc9Vb8Nm?usp=sharing
Auch als Variante, das Maskottchen BOMMEL gegen das Logo gelehnt ist, kann genutzt werden: https://ablage.wolkenfach.de/open?id=8MnbVcXz3LkJhGfDsApOiUyT1ReWq7Zxc
Das Thema 'Terminvereinbarung' soll sofort erfasst werden mittels des Layouts bzw. der grafischen Elemente.
Auch die Branchen-Icons ( https://ablage.wolkenfach.de/ordner/folders/4ZaQwSxEdCrFvTgByHnUjMiKoLp9PmNbq?usp=sharing ) dürfen verwendet werden.

```html
<!DOCTYPE html>
<html lang="de">
<head>
<meta charset="utf-8">
<title>Buchlotte – Geschäftspapiere</title>
<link href="https://fonts.googleapis.com/css2?family=Lato:wght@400;700&display=swap" rel="stylesheet">
<style>
:root{
  --bg:#3d3e41;
  --paper:#f4f5f4;
  --green:#8cc63f;
  --green-dark:#6fa52b;
  --ink:#5a5c5f;
  --ink-soft:#8a8c8f;
  --navy:#3a4a8a;
  --card-grey:#8d8f92;
}
*{box-sizing:border-box;margin:0;padding:0}
html,body{width:1200px;height:801px;overflow:hidden}
body{background:var(--bg);font-family:'Lato',sans-serif;color:var(--ink);position:relative}
.sheet{position:absolute;background:var(--paper);box-shadow:0 6px 18px rgba(0,0,0,.35);overflow:hidden}
.brand{display:flex;align-items:center;gap:8px}
.brand-mark{width:22px;height:22px;background:var(--green)}
.brand-name{font-weight:700;font-size:30px;color:var(--green-dark);line-height:1}
.brand-tag{font-size:10px;color:var(--ink-soft);margin-left:30px;margin-top:2px}

/* letterhead */
.letterhead{left:40px;top:47px;width:500px;height:707px;padding:40px 44px}
.letter-body{margin-top:34px;font-size:8.5px;line-height:1.55;color:var(--ink);position:relative;z-index:1}
.letter-body p{margin-bottom:11px}
.watermark-area{position:absolute;right:40px;top:190px;width:170px;height:300px;border-radius:40px;
  background:radial-gradient(ellipse at center,rgba(140,198,63,.16),rgba(140,198,63,0) 70%)}
.signoff{margin-top:16px;font-size:8.5px}
.signoff .sig{font-style:italic;font-size:16px;margin:8px 0 2px;color:#333}
.letter-foot{position:absolute;left:0;bottom:0;width:100%;height:110px}
.letter-foot svg{position:absolute;left:0;bottom:0}
.contact{position:absolute;bottom:46px;display:flex;gap:40px;right:44px;font-size:7.5px;line-height:1.5}
.contact b{color:var(--navy);font-size:7px;letter-spacing:.04em;display:block}

/* envelope back */
.env-back{left:590px;top:40px;width:570px;height:250px}
.env-back svg{position:absolute;inset:0}
/* envelope front */
.env-front{left:590px;top:310px;width:570px;height:260px;padding:28px 32px}
.window{position:absolute;right:32px;top:34px;width:190px;height:90px;border:1px solid #9aa0c0;border-radius:8px}
.env-front .contact{left:32px;right:auto;bottom:26px;gap:48px}

/* cards */
.card{top:598px;width:270px;height:156px}
.card-front{left:590px;background:linear-gradient(135deg,#d8d9da,#a9abad)}
.card-front .brand{position:absolute;left:50px;top:62px}
.card-front .brand-name{font-size:24px}
.card-back{left:890px}
.card-head{height:70px;background:var(--card-grey);display:flex;align-items:center;justify-content:space-between;padding:0 16px}
.card-head .brand-name{color:#fff;font-size:18px}
.card-head .brand-mark{width:14px;height:14px;background:#fff}
.person{color:#fff;text-align:right;font-size:11px;font-weight:700}
.person span{display:block;font-weight:400;font-size:8px;color:#e2e4e6}
.card-info{display:flex;justify-content:space-between;padding:20px 16px;font-size:7.5px;line-height:1.5}
.card-info div{text-align:center}
.dot{display:inline-block;width:10px;height:10px;border-radius:50%;background:var(--ink);margin-bottom:4px}
</style>
</head>
<body>

<section class="sheet letterhead">
  <div class="brand"><span class="brand-mark"></span><span class="brand-name">Buchlotte</span></div>
  <div class="brand-tag">Tool by datumsgriff.de</div>
  <div class="watermark-area" role="img" aria-label="Faint decorative illustration in soft green"></div>
  <div class="letter-body">
    <p>DEAR CLIENT,</p>
    <p>Lorem ipsum dolor sit amet, consectetur adipisicing elit, sed do eiusmod tempor incididunt ut labore et dolore magna aliqua. Ut enim ad minim veniam, quis nostrud exercitation ullamco laboris nisi ut aliquip ex ea commodo consequat. Duis aute irure dolor in reprehenderit in voluptate velit esse cillum dolore eu fugiat nulla pariatur. Excepteur sint occaecat cupidatat non proident, sunt in culpa qui officia deserunt mollit anim id est laborum.</p>
    <p>Lorem ipsum dolor sit amet, consectetur adipisicing elit, sed do eiusmod tempor incididunt ut labore et dolore magna aliqua. Ut enim ad minim veniam, quis nostrud exercitation ullamco laboris nisi ut aliquip ex ea commodo consequat. Duis aute irure dolor in reprehenderit in voluptate velit esse cillum dolore eu fugiat nulla pariatur. Excepteur sint occaecat cupidatat non proident, sunt in culpa qui officia deserunt mollit anim id est laborum.</p>
    <p>Lorem ipsum dolor sit amet, consectetur adipisicing elit, sed do eiusmod tempor incididunt ut labore et dolore magna aliqua. Ut enim ad minim veniam, quis nostrud exercitation ullamco laboris nisi ut aliquip ex ea commodo consequat. Duis aute irure dolor in reprehenderit in voluptate velit esse cillum dolore eu fugiat nulla pariatur.</p>
    <p>Lorem ipsum dolor sit amet, consectetur adipisicing elit, sed do eiusmod tempor incididunt ut labore et dolore magna aliqua. Ut enim ad minim veniam, quis nostrud exercitation ullamco laboris nisi ut aliquip ex ea commodo consequat. Excepteur sint occaecat cupidatat non proident, sunt in culpa qui officia deserunt mollit anim id est laborum.</p>
    <div class="signoff">Yours Sincerely,<div class="sig">Konrad</div>Konrad<br>Executive manager</div>
  </div>
  <div class="letter-foot">
    <svg width="500" height="110" viewBox="0 0 500 110"><polygon points="0,110 0,70 500,38 500,110" fill="var(--green)"/></svg>
    <div class="contact" style="bottom:80px">
      <div><b>ADRESS</b>Street, Region, Country<br>PO BOX 321</div>
      <div><b>TELEPHONE &amp; FAX</b>+49 (0) 40 555 010 20<br>+49 (0) 40 555 010 21</div>
      <div><b>WEB</b>info@beispielfirma.de<br>www.beispielfirma.de</div>
    </div>
  </div>
</section>

<section class="sheet env-back">
  <svg width="570" height="250" viewBox="0 0 570 250">
    <polygon points="0,0 570,0 285,120" fill="var(--green)"/>
    <g fill="#ffffff" stroke="#6b6e71" stroke-width="3">
      <circle cx="85" cy="185" r="22"/><circle cx="165" cy="185" r="22"/><circle cx="245" cy="185" r="22"/>
      <circle cx="325" cy="185" r="22"/><circle cx="405" cy="185" r="22"/><circle cx="485" cy="185" r="22"/>
    </g>
    <g fill="var(--green)"><circle cx="85" cy="185" r="8"/><rect x="159" y="175" width="12" height="20" rx="2"/>
      <path d="M238 176 l14 18 M252 176 l-14 18" stroke="var(--green)" stroke-width="3"/>
      <rect x="318" y="174" width="3" height="22"/><rect x="329" y="174" width="3" height="22"/>
      <path d="M405 173 l10 5 v8 c0 6 -5 10 -10 12 c-5 -2 -10 -6 -10 -12 v-8z"/>
      <rect x="477" y="177" width="16" height="16" rx="2"/></g>
  </svg>
</section>

<section class="sheet env-front">
  <div class="brand"><span class="brand-mark"></span><span class="brand-name">Buchlotte</span></div>
  <div class="brand-tag">Tool by datumsgriff.de</div>
  <div class="window"></div>
  <div class="contact">
    <div><b>ADRESS</b>Street, Region, Country<br>PO BOX 321</div>
    <div><b>TELEPHONE &amp; FAX</b>+49 (0) 40 555 010 20<br>+49 (0) 40 555 010 21</div>
    <div><b>WEB</b>info@beispielfirma.de<br>www.beispielfirma.de</div>
  </div>
</section>

<section class="sheet card card-front">
  <div class="brand"><span class="brand-mark"></span><span class="brand-name">Buchlotte</span></div>
</section>

<section class="sheet card card-back">
  <div class="card-head">
    <div class="brand"><span class="brand-mark"></span><span class="brand-name">Buchlotte</span></div>
    <div class="person">Mira Holt<span>Creative Director</span></div>
  </div>
  <div class="card-info">
    <div><span class="dot"></span><br>12 Hafenweg<br>Nordstadt 20095</div>
    <div><span class="dot"></span><br>+49 40 555 010<br>+49 40 555 011</div>
    <div><span class="dot"></span><br>mira@beispielfirma.de<br>www.beispielfirma.de</div>
  </div>
</section>

</body>
</html>
```